FinTech company looking to revamp and expand client-facing interface for our financial models

Pellworth Engines currently has a very simple website that allows clients to interact with our financial models. We are looking to completely redesign the current site and add several extra pages to provide extra functionality. We want the design to have a modern, slick feel, that will work on both a desktop or a tablet. It should be straightforward for clients to move between different pages at any time, and clear from the layout how to interact with the more advanced features. We have included screenshots of existing pages in the attached design brief, as well as sketches of the functionality required by the new pages, but can't provide a direct link to the current site.
Target Market(s)
Professional investors that will be paying to access the interface
Industry/Entity Type
Finance
Number of Pages Required
4 page
Colors
Designer to choose colors to be used in the design.
Look and feel
Each slider illustrates characteristics of the customer's brand and the style your logo design should communicate.

```html
<!DOCTYPE html>
<html lang="en">
<head>
<meta charset="utf-8">
<title>Pellworth Engines – Factors Dashboard</title>
<link href="https://fonts.googleapis.com/css2?family=Roboto:wght@400;500;700;900&display=swap" rel="stylesheet">
<style>
  :root {
    --brand-red: #e8284f;
    --ink: #2b2b2b;
    --ink-soft: #444;
    --canvas: #f3f4f7;
    --panel: #ffffff;
    --workspace: #e6e9f2;
    --row-alt: #ececec;
    --nav-active: #efefef;
    --divider: #e3e3e3;
    --search-border: #2d3142;
    --online: #3cb44b;
  }
  * { box-sizing: border-box; margin: 0; padding: 0; }
  html, body {
    width: 1069px; height: 1200px; overflow: hidden;
    background: var(--canvas);
    font-family: "Roboto", Arial, sans-serif;
    color: var(--ink);
  }
  .dashboard {
    position: absolute; left: 34px; top: 321px;
    width: 1000px; height: 558px;
    background: var(--panel);
    box-shadow: 0 6px 24px rgba(30, 40, 70, .08);
  }

  /* Header */
  .brand {
    position: absolute; left: 40px; top: 21px;
    font-size: 21px; font-weight: 900; letter-spacing: .5px;
    color: var(--brand-red);
  }
  .top-nav {
    position: absolute; left: 232px; top: 26px;
    display: flex; gap: 24px; font-size: 13.5px; font-weight: 400;
  }
  .top-nav .active { color: var(--brand-red); }
  .search {
    position: absolute; left: 754px; top: 19px;
    width: 209px; height: 35px;
    border: 1.5px solid var(--search-border); border-radius: 18px;
    display: flex; align-items: center; padding-left: 17px;
    font-size: 13px; color: var(--ink);
  }
  .search-btn {
    position: absolute; right: 3px; top: 3.5px;
    width: 26px; height: 26px; border-radius: 50%;
    background: var(--brand-red);
    display: flex; align-items: center; justify-content: center;
  }

  /* Sidebar */
  .sidebar { position: absolute; left: 0; top: 68px; width: 223px; }
  .avatar {
    position: absolute; left: 81px; top: 10px;
    width: 62px; height: 62px; border-radius: 50%;
    border: 3px solid var(--brand-red);
    background: radial-gradient(circle at 50% 40%, #d7b49c, #8a6b5c 70%, #4a4f5a);
  }
  .avatar-status {
    position: absolute; left: 130px; top: 61px;
    width: 9px; height: 9px; border-radius: 50%;
    background: var(--online); border: 1.5px solid #fff;
  }
  .user-name {
    position: absolute; left: 0; width: 223px; top: 83px;
    text-align: center; font-size: 13.5px; color: var(--brand-red);
  }
  .user-name svg { vertical-align: middle; margin-left: 3px; }
  .side-nav { position: absolute; left: 0; top: 111px; width: 223px; list-style: none; }
  .side-nav li {
    height: 37px; display: flex; align-items: center;
    font-size: 12px; color: var(--ink);
  }
  .side-nav li svg { margin-right: 11px; }
  .side-nav .section { padding-left: 36px; text-transform: uppercase; }
  .side-nav .sub { padding-left: 64px; }
  .side-nav .current { background: var(--nav-active); }

  /* Workspace */
  .workspace {
    position: absolute; left: 223px; top: 68px;
    width: 777px; height: 450px;
    background: var(--workspace);
  }
  .thresholds { position: absolute; left: 10px; top: 17px; display: flex; gap: 10px; }
  .threshold label { display: block; font-size: 11px; margin-bottom: 6px; }
  .threshold .field {
    width: 180px; height: 34px; background: #fff;
    display: flex; align-items: center; padding-left: 11px; font-size: 12.5px;
  }
  .results {
    position: absolute; left: 10px; top: 88px;
    width: 757px; height: 344px;
    background: #fff; border-radius: 4px; overflow: hidden;
  }
  .export {
    height: 44px; display: flex; align-items: center; padding-left: 22px;
    font-size: 14px; font-weight: 500; color: var(--brand-red);
  }
  .export svg { margin-left: 7px; }
  table { width: 100%; border-collapse: collapse; table-layout: fixed; }
  th {
    height: 43px; background: var(--row-alt);
    color: var(--brand-red); font-size: 13.5px; font-weight: 500;
  }
  td {
    height: 51.4px; text-align: center; font-size: 10.5px; color: var(--ink-soft);
  }
  th + th, td + td { border-left: 1px solid var(--divider); }
  tbody tr:nth-child(even) td { background: var(--row-alt); }

  .footer {
    position: absolute; left: 223px; width: 777px; top: 525px;
    text-align: center; font-size: 12px; color: var(--ink-soft);
  }
</style>
</head>
<body>
<main class="dashboard">
  <header>
    <div class="brand">PELLWORTH</div>
    <nav class="top-nav">
      <span>FACTORS</span>
      <span class="active">250D</span>
      <span>83D</span>
      <span>42D</span>
    </nav>
    <div class="search">Search
      <span class="search-btn">
        <svg width="11" height="11" viewBox="0 0 12 12"><circle cx="5" cy="5" r="3.4" fill="none" stroke="#fff" stroke-width="1.6"/><line x1="7.5" y1="7.5" x2="10.5" y2="10.5" stroke="#fff" stroke-width="1.8" stroke-linecap="round"/></svg>
      </span>
    </div>
  </header>

  <aside class="sidebar">
    <div class="avatar" role="img" aria-label="Portrait photo of the signed-in user"></div>
    <span class="avatar-status"></span>
    <div class="user-name">Daniel Hart<svg width="8" height="5" viewBox="0 0 8 5"><path d="M0 0h8L4 5z" fill="#e8284f"/></svg></div>
    <ul class="side-nav">
      <li class="section current"><svg width="13" height="12" viewBox="0 0 13 12"><path d="M6.5 0L0 6h2v6h3.5V8h2v4H11V6h2z" fill="#2b2b2b"/></svg>Home</li>
      <li class="section"><svg width="13" height="12" viewBox="0 0 13 12"><rect x="0" y="5" width="3" height="7" fill="#2b2b2b"/><path d="M4 5l3-5c1.2 0 1.8.8 1.5 2L8 4h4c.8 0 1.2.7 1 1.4l-1.5 5.6c-.2.6-.6 1-1.2 1H4z" fill="#2b2b2b"/></svg>Models</li>
      <li class="sub"><svg width="12" height="12" viewBox="0 0 12 12"><circle cx="6" cy="6" r="6" fill="#2b2b2b"/><path d="M3 6h5M6 3.5L8.5 6 6 8.5" fill="none" stroke="#fff" stroke-width="1.5"/></svg>Equities</li>
      <li class="sub"><svg width="12" height="12" viewBox="0 0 12 12"><circle cx="6" cy="6" r="6" fill="#2b2b2b"/><path d="M3 6h5M6 3.5L8.5 6 6 8.5" fill="none" stroke="#fff" stroke-width="1.5"/></svg>ETFS</li>
      <li class="sub"><svg width="12" height="12" viewBox="0 0 12 12"><circle cx="6" cy="6" r="6" fill="#2b2b2b"/><path d="M3 6h5M6 3.5L8.5 6 6 8.5" fill="none" stroke="#fff" stroke-width="1.5"/></svg>Pairs</li>
      <li class="sub"><svg width="12" height="12" viewBox="0 0 12 12"><circle cx="6" cy="6" r="6" fill="#2b2b2b"/><path d="M3 6h5M6 3.5L8.5 6 6 8.5" fill="none" stroke="#fff" stroke-width="1.5"/></svg>ETF Pairs</li>
      <li class="sub"><svg width="12" height="12" viewBox="0 0 12 12"><circle cx="6" cy="6" r="6" fill="#2b2b2b"/><path d="M3 6h5M6 3.5L8.5 6 6 8.5" fill="none" stroke="#fff" stroke-width="1.5"/></svg>Factors</li>
      <li class="section"><svg width="12" height="12" viewBox="0 0 12 12"><circle cx="6" cy="6" r="4.2" fill="none" stroke="#2b2b2b" stroke-width="3" stroke-dasharray="2.2 1.1"/><circle cx="6" cy="6" r="3.2" fill="#2b2b2b"/><circle cx="6" cy="6" r="1.4" fill="#fff"/></svg>Sensitivities</li>
      <li class="section"><svg width="13" height="12" viewBox="0 0 13 12"><path d="M6.5 0l1.9 4 4.1.4-3.1 2.8.9 4.3-3.8-2.3-3.8 2.3.9-4.3L.5 4.4 4.6 4z" fill="#2b2b2b"/></svg>Favourites</li>
    </ul>
  </aside>

  <section class="workspace">
    <div class="thresholds">
      <div class="threshold"><label>Stat 1 Threshold</label><div class="field">-10</div></div>
      <div class="threshold"><label>Stat 2 Threshold</label><div class="field">-10</div></div>
      <div class="threshold"><label>Stat 3 Threshold</label><div class="field">-10</div></div>
    </div>
    <div class="results">
      <div class="export">Export
        <svg width="15" height="14" viewBox="0 0 15 14"><path d="M11 8v4.5H1.5V3H6" fill="none" stroke="#e8284f" stroke-width="1.6"/><path d="M8.5 1h5v5M13.5 1L6.5 8" fill="none" stroke="#e8284f" stroke-width="1.6"/></svg>
      </div>
      <table>
        <thead>
          <tr><th>Factor</th><th>ID</th><th>Sector</th><th>Stat 1</th><th>Stat 2</th><th>Stat 3</th><th>Stat 4</th><th>Stat 5</th><th>Stat 6</th></tr>
        </thead>
        <tbody>
          <tr><td>Factor 1</td><td>Model 1</td><td>Materials</td><td>-1.4</td><td>0.1</td><td>-3.1</td><td>-1.4</td><td>0.1</td><td>-3.1</td></tr>
          <tr><td>Factor 1</td><td>Model 1</td><td>Materials</td><td>2.8</td><td>0.1</td><td>6.1</td><td>2.8</td><td>0.1</td><td>6.1</td></tr>
          <tr><td>Factor 1</td><td>Model 1</td><td>Materials</td><td>-3.7</td><td>2.7</td><td>-7.2</td><td>-3.7</td><td>2.7</td><td>-7.2</td></tr>
          <tr><td>Factor 1</td><td>Model 1</td><td>Materials</td><td>2.8</td><td>0.2</td><td>2.7</td><td>2.8</td><td>0.2</td><td>2.7</td></tr>
          <tr><td>Factor 1</td><td>Model 1</td><td>Materials</td><td>0.8</td><td>0.3</td><td>2.5</td><td>0.8</td><td>0.3</td><td>2.5</td></tr>
        </tbody>
      </table>
    </div>
  </section>

  <footer class="footer">Copyrights © 2019. All rights reserved</footer>
</main>
</body>
</html>
```